Business card design needed

I have a leadership coaching and consultancy business which specialises in the education sector. I would like a clean, professional design). The design needs to speak to strength, support, new learning, connections & a growth mindest.

I am also looking for a unique LOGO. This is very important.

Target Market(s)

Educational Leaders & executives

Industry/Entity Type

Leadership

Contact Information for Business Card

Marnie Holbrook
Principal Coach & Consultant
Marnie Holbrook Coaching & Consulting
0491 263 814
marnie.holbrook@vendamail.example
I also would like my friendspace, twitter and workline accounts to appear

Logo styles of interest
Lettermark Logo
Requirements
Must have
• A 2 sided business card with contact details on the back
A logo

```html
<!DOCTYPE html>
<html lang="en">
<head>
<meta charset="utf-8">
<title>Marnie Holbrook Coaching &amp; Consulting — Business Card</title>
<link rel="stylesheet" href="https://fonts.googleapis.com/css2?family=Open+Sans:wght@600;700;800&display=swap">
<style>
  :root {
    --orange: #f26122;
    --white: #ffffff;
    --stage: #dcdcdc;
  }
  * { box-sizing: border-box; margin: 0; padding: 0; }
  html, body {
    width: 1200px; height: 985px; overflow: hidden;
    background: var(--stage);
    font-family: "Open Sans", Arial, sans-serif;
  }
  .canvas { position: relative; width: 1200px; height: 985px; }
  .card {
    position: absolute; left: 220px; width: 760px; height: 420px;
    border-radius: 28px; overflow: hidden;
    box-shadow: 0 6px 18px rgba(0,0,0,0.18);
  }
  .brand-dot { border-radius: 50%; flex: none; }
  .brand-name { font-weight: 700; line-height: 1.15; white-space: nowrap; }

  /* Front side */
  .card--front { top: 50px; background: var(--orange); }
  .front-brand {
    position: absolute; inset: 0;
    display: flex; align-items: center; justify-content: center; gap: 22px;
  }
  .front-brand .brand-dot { width: 74px; height: 74px; background: var(--white); }
  .front-brand .brand-name { color: var(--white); font-size: 30px; }

  /* Back side */
  .card--back { top: 515px; background: var(--white); }
  .back-brand {
    position: absolute; left: 30px; top: 0; bottom: 0; width: 262px;
    display: flex; align-items: center; gap: 12px;
  }
  .back-brand .brand-dot { width: 44px; height: 44px; background: var(--orange); }
  .back-brand .brand-name { color: var(--orange); font-size: 18px; }
  .divider-line {
    position: absolute; left: 300px; top: 0; bottom: 0; width: 10px;
    background: var(--orange);
  }
  .contact-panel {
    position: absolute; left: 320px; right: 0; top: 0; bottom: 0;
    background: var(--orange); color: var(--white);
    padding: 46px 24px 0 34px;
  }
  .person-name { font-size: 34px; font-weight: 800; letter-spacing: 1px; line-height: 1.1; white-space: nowrap; }
  .person-role { font-size: 20px; font-weight: 700; margin-top: 8px; }
  .person-company { font-size: 15px; font-weight: 600; margin-top: 6px; }
  .contact-list { list-style: none; margin-top: 30px; }
  .contact-list li {
    display: flex; align-items: center; gap: 12px;
    font-size: 16px; font-weight: 700; line-height: 1; margin-bottom: 13px;
    white-space: nowrap;
  }
  .contact-icon {
    width: 20px; height: 20px; flex: none;
    border: 2px solid var(--white); border-radius: 3px;
    display: flex; align-items: center; justify-content: center;
  }
</style>
</head>
<body>
<main class="canvas">
  <section class="card card--front" aria-label="Business card front">
    <div class="front-brand">
      <span class="brand-dot"></span>
      <p class="brand-name">Marnie Holbrook<br>Coaching &amp; Consulting</p>
    </div>
  </section>

  <section class="card card--back" aria-label="Business card back">
    <div class="back-brand">
      <span class="brand-dot"></span>
      <p class="brand-name">Marnie Holbrook<br>Coaching &amp; Consulting</p>
    </div>
    <div class="divider-line"></div>
    <div class="contact-panel">
      <h1 class="person-name">Marnie Holbrook</h1>
      <p class="person-role">Principal Coach &amp; Consultant</p>
      <p class="person-company">Marnie Holbrook Coaching &amp; Consulting</p>
      <ul class="contact-list">
        <li>
          <span class="contact-icon">
            <svg width="12" height="12" viewBox="0 0 12 12"><path d="M2.5 1h2l1 3-1.4 1a6 6 0 0 0 2.9 2.9l1-1.4 3 1v2a1 1 0 0 1-1 1A9 9 0 0 1 1.5 2a1 1 0 0 1 1-1z" fill="#fff"/></svg>
          </span>0491 263 814
        </li>
        <li>
          <span class="contact-icon">
            <svg width="12" height="10" viewBox="0 0 12 10"><rect x="0.5" y="0.5" width="11" height="9" fill="none" stroke="#fff"/><path d="M0.5 0.5 6 5.5 11.5 0.5" fill="none" stroke="#fff"/></svg>
          </span>marnie.holbrook@vendamail.example
        </li>
        <li>
          <span class="contact-icon">
            <svg width="12" height="12" viewBox="0 0 12 12"><path d="M5 7 7 5M4.2 5.3 2.8 6.7a1.8 1.8 0 0 0 2.5 2.5l1.4-1.4M7.8 6.7l1.4-1.4a1.8 1.8 0 0 0-2.5-2.5L5.3 4.2" fill="none" stroke="#fff" stroke-width="1.4" stroke-linecap="round"/></svg>
          </span>your friendspace link here
        </li>
        <li>
          <span class="contact-icon">
            <svg width="12" height="12" viewBox="0 0 12 12"><path d="M5 7 7 5M4.2 5.3 2.8 6.7a1.8 1.8 0 0 0 2.5 2.5l1.4-1.4M7.8 6.7l1.4-1.4a1.8 1.8 0 0 0-2.5-2.5L5.3 4.2" fill="none" stroke="#fff" stroke-width="1.4" stroke-linecap="round"/></svg>
          </span>your chirper link here
        </li>
        <li>
          <span class="contact-icon">
            <svg width="12" height="12" viewBox="0 0 12 12"><path d="M5 7 7 5M4.2 5.3 2.8 6.7a1.8 1.8 0 0 0 2.5 2.5l1.4-1.4M7.8 6.7l1.4-1.4a1.8 1.8 0 0 0-2.5-2.5L5.3 4.2" fill="none" stroke="#fff" stroke-width="1.4" stroke-linecap="round"/></svg>
          </span>your workline link here
        </li>
      </ul>
    </div>
  </section>
</main>
</body>
</html>
```